Förderverein einer Kirchengemeinde sucht Flyer-Design
Zielgruppe
Wir sind ein Förderverein einer Kirchengemeinde, der sich für die kirchenmusikalische Arbeit einsetzt.
Wir wünschen uns ein niveauvolles und zeitgemäßes/modernes Flyerdesign, das die etablierten Konzertbesucher anspricht, aber vor allem auch Menschen erreicht und überzeugt, die (noch) nichts mit Kirche zu tun haben.
Das Alter der (Haupt-) Zielgruppe (Männer und Frauen) erstreckt sich von 45 bis 70 Jahren.
Aufgabenstellung
Bei der Wahl des Formates würden wir (aus der Sicht von Laien) ein zweimal gefaltetes DIN A4 quer Format nehmen. Aber wir lassen uns gerne überraschen und sind grundsätzlich für andere Lösungen offen.
Bitte den Abschnitt für Adress- und sonstige Dateneintragungen samt Kontodaten so gestalten und platzieren, dass man ihn leicht abtrennen und verschicken kann.
Der Flyer soll Kirchenmusik als lebendig und attraktiv darstellen und neue (jüngere) Mitglieder für den Freundeskreis werben.
Lassen Sie die Bilder sprechen!!

```html
<!DOCTYPE html>
<html lang="de">
<head>
<meta charset="utf-8">
<title>Kirchenmusik braucht Freunde</title>
<link rel="stylesheet" href="https://fonts.googleapis.com/css2?family=Fira+Sans:wght@600;700&family=Raleway:wght@400&display=swap">
<style>
  :root {
    --red: #c1161d;
    --text: #4a4a4a;
    --paper: #ffffff;
  }
  * { margin: 0; padding: 0; box-sizing: border-box; }
  html, body { width: 1200px; height: 846px; overflow: hidden; background: var(--paper); }
  .flyer-page { position: relative; width: 1200px; height: 846px; background: var(--paper); overflow: hidden; }
  .photo-column { position: absolute; left: 0; top: 0; }
  .headline {
    position: absolute; right: 522px; top: 98px;
    font-family: "Fira Sans", sans-serif; font-weight: 700;
    font-size: 34px; line-height: 42px; color: var(--red); text-align: right;
  }
  .divider { position: absolute; left: 698px; top: 98px; width: 2px; height: 180px; background: var(--red); }
  .intro, .benefit-line {
    position: absolute; font-family: "Raleway", sans-serif; font-weight: 400;
    color: var(--text); white-space: nowrap; font-variant-numeric: lining-nums;
  }
  .intro { left: 719px; font-size: 20px; line-height: 30px; letter-spacing: 0.2px; }
  .intro-text { top: 109px; }
  .intro-invite { top: 246px; }
  .benefits-title {
    position: absolute; left: 468px; top: 336px;
    font-family: "Fira Sans", sans-serif; font-weight: 600;
    font-size: 26px; line-height: 32px; color: var(--red);
  }
  .benefit-line { font-size: 19.5px; line-height: 26px; }
</style>
</head>
<body>
<main class="flyer-page">
  <svg class="photo-column" width="530" height="846" viewBox="0 0 530 846">
    <defs>
      <clipPath id="photo-wedge"><polygon points="0,0 322,0 518,846 0,846"/></clipPath>
      <linearGradient id="brass" x1="0" y1="0" x2="1" y2="1">
        <stop offset="0" stop-color="#b99a5a"/><stop offset="0.5" stop-color="#7b6550"/><stop offset="1" stop-color="#3c3a44"/>
      </linearGradient>
      <linearGradient id="hedge-flutes" x1="0" y1="0" x2="0" y2="1">
        <stop offset="0" stop-color="#2f4a26"/><stop offset="0.55" stop-color="#7a8a7e"/><stop offset="1" stop-color="#6f7a52"/>
      </linearGradient>
      <linearGradient id="hedge-choir" x1="0" y1="0" x2="0" y2="1">
        <stop offset="0" stop-color="#28401f"/><stop offset="0.35" stop-color="#c9b232"/><stop offset="0.85" stop-color="#b5ad8c"/><stop offset="1" stop-color="#6d6a4e"/>
      </linearGradient>
    </defs>
    <polygon points="322,0 338,0 530,846 518,846" fill="#d9d9d9" opacity="0.6"/>
    <g clip-path="url(#photo-wedge)">
      <rect x="0" y="0" width="530" height="252" fill="url(#brass)" role="img" aria-label="Foto: Hände an einer goldenen Trompete"/>
      <rect x="0" y="252" width="530" height="306" fill="url(#hedge-flutes)" role="img" aria-label="Foto: Flötenensemble mit Blockflöten vor einer Hecke"/>
      <rect x="0" y="558" width="530" height="288" fill="url(#hedge-choir)" role="img" aria-label="Foto: Kinderchor in gelben T-Shirts vor einer Hecke"/>
      <rect x="0" y="251" width="530" height="2" fill="#ffffff"/>
      <rect x="0" y="557" width="530" height="2" fill="#ffffff"/>
    </g>
  </svg>

  <h1 class="headline">Kirchenmusik<br>braucht Freunde</h1>
  <div class="divider"></div>

  <p class="intro intro-text">Im Jahr 1999 gegründet, unterstützt<br>der Freundeskreis Kirchenmusik die<br>vielfältigen musikalischen Aktivitäten<br>an der St. Aegidien-Kirche.</p>
  <p class="intro intro-invite">Wir laden Sie ein, Mitglied zu werden!</p>

  <h2 class="benefits-title">Mit Ihrem Beitrag …</h2>

  <div class="benefit-line" style="left:476px;top:397px">… bereichern Sie Wendelstedts kulturelle Landschaft durch den Erhalt</div>
  <div class="benefit-line" style="left:506px;top:423px">und Ausbau unseres hohen kirchenmusikalischen Niveaus</div>

  <div class="benefit-line" style="left:493px;top:468px">… stärken Sie das Ehrenamt</div>

  <div class="benefit-line" style="left:504px;top:512px">… ermöglichen Sie der Kantorei, dem Posaunenchor, dem</div>
  <div class="benefit-line" style="left:533px;top:539px">Kinderchor und dem Flötenensemble regelmäßige Proben-</div>
  <div class="benefit-line" style="left:536px;top:565px">arbeit, Probenwochenenden und die Anschaffung von</div>
  <div class="benefit-line" style="left:543px;top:591px">Notenmaterial</div>

  <div class="benefit-line" style="left:532px;top:636px">… erhalten Sie die historische Konrad Helmer Orgel von 1748</div>

  <div class="benefit-line" style="left:541px;top:681px">… fördern Sie die Ausbildung kirchenmusikalischen Nach-</div>
  <div class="benefit-line" style="left:568px;top:707px">wuchses</div>
</main>
</body>
</html>
```